Brand Identity Stationary Package

Hello I'm looking for a full branding package for my Property Management Company. I have a logo but looking to have the following
Business Card
Email signature
Facebook cover photo
Letterhead (word.doc)
#10 Envelope
Pocket Folder - link to 9x12 pocket folder design specs https://www.printorbit-example.ca/marketing-materials/presentation-folders
would like everything to match and be brand identifiable. The company looks after residential properties/apartments and some commercial properties. Attached is a zip of the files.
For Business Card
Name: Gareth Lindqvist
Position: Operations Manager
Number: 1 (555) 384-2917
Email: Gareth@harborkey-example.ca
Website: Harborkey-example.ca
Property Management

```html
<!DOCTYPE html>
<html lang="en">
<head>
<meta charset="utf-8">
<title>Harborkey Envelope</title>
<link href="https://fonts.googleapis.com/css2?family=Montserrat:wght@600&family=Source+Sans+3:wght@400&display=swap" rel="stylesheet">
<style>
  :root {
    --backdrop: #d2d2d2;
    --paper: #f6f6f6;
    --brand-green: #80a541;
    --ink: #111111;
    --white: #ffffff;
  }
  * { margin: 0; padding: 0; box-sizing: border-box; }
  html, body { width: 1200px; height: 1050px; overflow: hidden; }
  body { background: var(--backdrop); position: relative; font-family: "Source Sans 3", sans-serif; }

  .envelope {
    position: absolute;
    left: 145px;
    width: 910px;
    height: 390px;
    background: var(--paper);
    overflow: hidden;
  }
  .envelope--back { top: 105px; }
  .envelope--front { top: 556px; }
  .envelope svg.art { position: absolute; inset: 0; width: 910px; height: 390px; }

  .wordmark {
    position: absolute;
    font-family: "Montserrat", sans-serif;
    font-weight: 600;
    line-height: 1;
  }
  .wordmark__name { display: block; letter-spacing: 6px; }
  .wordmark__tag { display: block; letter-spacing: 8.4px; margin-top: 10px; font-size: 10px; }

  .envelope--back .wordmark {
    top: 36px; left: 0; width: 910px; text-align: center; color: var(--white);
  }
  .envelope--back .wordmark__name { font-size: 40px; }

  .envelope--front .wordmark { top: 86px; left: 52px; color: var(--ink); }
  .envelope--front .wordmark__name { font-size: 33px; letter-spacing: 5px; }
  .envelope--front .wordmark__tag { font-size: 9px; margin-top: 8px; letter-spacing: 7.6px; }

  .contact-list {
    position: absolute; top: 168px; left: 52px; list-style: none;
    color: var(--ink); font-size: 20px; line-height: 26px;
  }
  .contact-list li { display: flex; align-items: center; }
  .contact-list svg { width: 16px; height: 16px; margin-right: 13px; flex: none; }
</style>
</head>
<body>

<section class="envelope envelope--back" aria-label="Envelope back">
  <svg class="art" viewBox="0 0 910 390" aria-hidden="true">
    <path fill="var(--brand-green)" d="M0 0 H910 L885 92 Q872 131 834 131 H76 Q38 131 25 92 Z"/>
  </svg>
  <div class="wordmark">
    <span class="wordmark__name">HARBORKEY</span>
    <span class="wordmark__tag">PROPERTY MANAGEMENT</span>
  </div>
</section>

<section class="envelope envelope--front" aria-label="Envelope front">
  <svg class="art" viewBox="0 0 910 390" aria-hidden="true">
    <polygon fill="var(--ink)" points="0,334 614,338 591,355 0,353"/>
    <polygon fill="var(--brand-green)" points="0,358 600,362 652,329 910,330 910,390 0,390"/>
  </svg>
  <div class="wordmark">
    <span class="wordmark__name">HARBORKEY</span>
    <span class="wordmark__tag">PROPERTY MANAGEMENT</span>
  </div>
  <ul class="contact-list">
    <li>
      <svg viewBox="0 0 16 16" aria-hidden="true"><path fill="var(--brand-green)" d="M1 6 Q8 1 15 6 L13 8 L11 6.5 V5.5 H5 V6.5 L3 8 Z M4 8 H12 L14 14 H2 Z"/></svg>
      1 (555) 384-2917
    </li>
    <li>
      <svg viewBox="0 0 16 16" aria-hidden="true"><rect x="1" y="3" width="14" height="10" fill="var(--brand-green)"/><path d="M1 3 L8 9 L15 3" fill="none" stroke="var(--paper)" stroke-width="1.2"/></svg>
      Gareth@harborkey-example.ca
    </li>
    <li>
      <svg viewBox="0 0 16 16" aria-hidden="true"><circle cx="8" cy="8" r="7" fill="var(--brand-green)"/><path d="M4 5 Q6 4 7 6 Q6 8 4 7 Z M9 9 Q12 8 12 11 Q10 13 9 11 Z" fill="var(--paper)"/></svg>
      www.Harborkey-example.ca
    </li>
  </ul>
</section>

</body>
</html>
```